High end Electrical/home automation Business Card

Need a card for a high end electrical and home automation company utilising the existing logo.
Phone
Email
Website

Like black look with raised detail. Don’t necessarily need to keep colour of logo it could be made grayscale or white etc

Target Market(s)

High end clients

Contact Information for Business Card

Brightmoor Electrical

Requirements
Must have
• Logo, phone, email, website, address

High end look
Nice to have
• Black background card
Raised font
Should not have
• Lots of colour

```html
<!DOCTYPE html>
<html lang="en">
<head>
<meta charset="utf-8">
<title>Brightmoor Electrical – Business Card</title>
<link rel="stylesheet" href="https://fonts.googleapis.com/css2?family=Work+Sans:wght@400;500;600&display=swap">
<style>
  :root {
    --page: #ecedee;
    --card-dark: #2c2b2c;
    --card-frost: #d7dadc;
    --text-light: #e4e2de;
    --text-muted: #cfccc7;
    --accent: #1a8fd6;
  }
  html, body {
    margin: 0;
    padding: 0;
    width: 1200px;
    height: 887px;
    overflow: hidden;
    background: var(--page);
    font-family: "Work Sans", Arial, sans-serif;
  }
  .card {
    position: absolute;
    left: 100px;
    top: 157px;
    width: 1000px;
    height: 572px;
    border-radius: 24px;
    overflow: hidden;
    background: var(--card-frost);
    box-shadow: 0 0 0 1px rgba(0,0,0,0.06);
  }
  .card-art {
    position: absolute;
    inset: 0;
  }
  .wordmark {
    position: absolute;
    left: 63px;
    top: 48px;
    margin: 0;
    font-size: 32px;
    font-weight: 600;
    letter-spacing: -0.5px;
    color: var(--text-light);
  }
  .accent-bar {
    position: absolute;
    left: 0;
    top: 242px;
    width: 20px;
    height: 62px;
    background: var(--accent);
  }
  .person {
    position: absolute;
    left: 61px;
    top: 236px;
    margin: 0;
  }
  .person-name {
    display: block;
    font-size: 35px;
    font-weight: 500;
    letter-spacing: 2.5px;
    color: var(--accent);
    line-height: 1;
  }
  .person-role {
    display: block;
    margin-top: 12px;
    font-size: 23px;
    font-weight: 400;
    letter-spacing: 0.5px;
    color: var(--text-muted);
  }
  .address {
    position: absolute;
    left: 60px;
    top: 322px;
    margin: 0;
    font-style: normal;
    font-size: 23px;
    line-height: 32px;
    letter-spacing: 0.8px;
    color: var(--text-muted);
  }
  .contact-list {
    position: absolute;
    left: 58px;
    top: 397px;
    margin: 0;
    padding: 0;
    list-style: none;
    font-size: 24px;
    line-height: 33px;
    letter-spacing: 0.8px;
    color: var(--text-muted);
  }
  .contact-list li {
    display: flex;
    align-items: center;
    gap: 8px;
  }
  .contact-icon {
    width: 16px;
    height: 16px;
    flex: none;
  }
</style>
</head>
<body>
  <div class="card">
    <svg class="card-art" width="1000" height="572" viewBox="0 0 1000 572" aria-hidden="true">
      <polygon points="0,0 772,0 500,572 0,572" fill="var(--card-dark)"/>
      <circle cx="790" cy="320" r="150" fill="none" stroke="var(--accent)" stroke-width="38"/>
    </svg>

    <p class="wordmark">Brightmoor Electrical</p>

    <div class="accent-bar"></div>
    <h1 class="person">
      <span class="person-name">DANIEL HAYES</span>
      <span class="person-role">Founder</span>
    </h1>

    <address class="address">418 Alder Crest Road<br>Colville, WA 99114</address>

    <ul class="contact-list">
      <li>
        <svg class="contact-icon" viewBox="0 0 16 16"><path d="M3.5 1.5l3 3-1.6 1.8c.8 1.8 2.2 3.3 4 4.2l1.8-1.6 3 3-1.8 2.2C6.6 13.6 2.3 9.4 1.4 3.3z" fill="var(--accent)"/></svg>
        555 014 2298
      </li>
      <li>
        <svg class="contact-icon" viewBox="0 0 16 16"><rect x="1.5" y="3.5" width="13" height="9" fill="none" stroke="var(--accent)" stroke-width="1.5"/><path d="M1.5 3.5l6.5 5 6.5-5" fill="none" stroke="var(--accent)" stroke-width="1.5"/></svg>
        hello@brightmoor.com
      </li>
      <li>
        <svg class="contact-icon" viewBox="0 0 16 16"><circle cx="8" cy="8" r="6.5" fill="none" stroke="var(--accent)" stroke-width="1.4"/><ellipse cx="8" cy="8" rx="2.8" ry="6.5" fill="none" stroke="var(--accent)" stroke-width="1.2"/><path d="M1.5 8h13" stroke="var(--accent)" stroke-width="1.2"/></svg>
        brightmoorelectric.com
      </li>
    </ul>
  </div>
</body>
</html>
```